Cover for Lanterns Along the Quiet Shore of Being

Cover for a book that describes everything that happens to a person, from pre-birth life plans through growing in compassion and wisdom to death and living in the afterlife. The information is revealed in messages from people living in the life after this life. The title is Lessons Gathered From Every Season of Your Existence: Shared by Voices Dwelling Beyond the Veil. Author is T. Wesley Prandt. Book size is 6 by 9.

Target Market(s)

General

Font styles to use
Serif

```html
<!DOCTYPE html>
<html lang="en">
<head>
<meta charset="utf-8">
<title>Lessons Gathered From Every Season of Your Existence — T. Wesley Prandt</title>
<link rel="stylesheet" href="https://fonts.googleapis.com/css2?family=Bebas+Neue&family=Montserrat:wght@500;600&family=Zilla+Slab:ital,wght@1,500&display=swap">
<style>
  :root {
    --sky-top: #0d1826;
    --sky-mid: #24364a;
    --sky-glow: #3f5467;
    --ridge: #070b12;
    --ink: #ffffff;
    --ink-soft: #e9edf2;
  }
  html, body {
    margin: 0;
    padding: 0;
    width: 800px;
    height: 1200px;
    overflow: hidden;
    background: var(--sky-top);
  }
  .cover {
    position: relative;
    width: 800px;
    height: 1200px;
    overflow: hidden;
    color: var(--ink);
  }
  .cover-backdrop {
    position: absolute;
    inset: 0;
    background:
      radial-gradient(ellipse 90% 45% at 55% 78%, var(--sky-glow) 0%, transparent 70%),
      linear-gradient(180deg, var(--sky-top) 0%, var(--sky-mid) 55%, var(--sky-glow) 76%, var(--ridge) 86%, var(--ridge) 100%);
  }
  .rule {
    position: absolute;
    left: 80px;
    width: 640px;
    height: 4px;
    background: var(--ink);
  }
  .rule--top { top: 62px; }
  .rule--under-author { top: 144px; }
  .rule--under-title { top: 752px; height: 7px; }
  .author {
    position: absolute;
    top: 86px;
    left: 0;
    width: 100%;
    margin: 0;
    text-align: center;
    font-family: "Montserrat", sans-serif;
    font-weight: 600;
    font-size: 25px;
    letter-spacing: 0.16em;
    text-transform: uppercase;
  }
  .title-block {
    position: absolute;
    top: 180px;
    left: 90px;
    width: 620px;
    margin: 0;
    text-align: center;
  }
  .title-main {
    display: block;
    font-family: "Bebas Neue", sans-serif;
    font-weight: 400;
    font-size: 88px;
    line-height: 0.98;
    letter-spacing: 0.06em;
    text-transform: uppercase;
  }
  .title-sub {
    display: block;
    margin-top: 22px;
    font-family: "Zilla Slab", serif;
    font-style: italic;
    font-weight: 500;
    font-size: 42px;
    line-height: 1.2;
    color: var(--ink-soft);
  }
  .blurb {
    position: absolute;
    top: 1060px;
    left: 100px;
    width: 600px;
    margin: 0;
    text-align: center;
    font-family: "Montserrat", sans-serif;
    font-weight: 500;
    font-size: 17px;
    line-height: 1.35;
    color: var(--ink-soft);
  }
</style>
</head>
<body>
  <main class="cover">
    <div class="cover-backdrop" role="img" aria-label="Starry night sky fading to a dark mountain ridge at the horizon"></div>

    <div class="rule rule--top"></div>
    <p class="author">T. Wesley Prandt</p>
    <div class="rule rule--under-author"></div>

    <h1 class="title-block">
      <span class="title-main">Lessons Gathered From Every Season of Your Existence:</span>
      <span class="title-sub">Shared by Voices Dwelling Beyond the Veil</span>
    </h1>

    <div class="rule rule--under-title"></div>

    <p class="blurb">Everything that happens to a person, from pre-birth life plans through growing in compassion and wisdom to death and living in the afterlife.</p>
  </main>
</body>
</html>
```